Australian Smart Home, Solar + Battery Company needs brochure to showcase Maple Dwelling Bundles

We are a home energy products and services provider and need a brochure to showcase the offerings we provide. There are few, if any competitors that offer the full suite of advanced technologies like we do, and we want to make it easy for customers to understand the benefits, trust in the company, and curious enough to give us a ring or request a quote online.

Size of Brochure: Tri-Fold 8.5" x 11". This is what I'm thinking, though if you find a bi-fold or quad fold would be better I'm open to that as well. The idea is we can use it as a brochure and as a PDF file we send to customers over email to get a basic understanding of the packages we offer. Another idea is a 2 or 4 page booklet like this: http://cdn.pixelvortaq.com/wp-content/uploads/2015/02/5-A4LandscapeBrochureMockup.jpg

We want to start the brochure with 3 Maple Dwelling Bundles, listing what's included at a high level and giving the customer a sense that the products can very effectively go together for the best results. Then we want to follow up pages that have a bit more information on each product we offer.

3 Maple Dwelling Bundles:

1) Basic Package:
-Solar Hybrid System (Battery Ready) with money back performance guarantee
-LED Lighting Retrofit
-Quill Smart Thermostat
-Whole Home Energy Monitoring with Mobile Phone Air Con control

2) Freedom Package
-Basic Package plus:
-Lithium Ion Battery Storage
-Backup Power Protection in case of a grid blackout

3) Total Control Package
-Freedom Package plus:
-Efficient hot water system: Solar Hot Water or High Efficiency Heat Pump
-Quill Guardo smoke & CO detection system with mobile phone alerts

Please see our website for an overview of the different products listed, and I've attached brochures for most of the products as well. The only one's that are not attached are the quill product and the LED lights. Please see the Quill website for graphics/taglines to use. Also the videos are a great way to understand how these products work.

Quill Thermostat: https://quillhaus.example/thermostat/life-with-quill-thermostat/
Quill Guardo: https://quillhaus.example/smoke-co-alarm/life-with-quill-guardo/

All logos we have are uploaded, let me know if you need another file format.

Maple Differentiators:
-Solar + Battery Specialists
-10 year warranty and 10 year money back performance guarantee
-Whole home solutions customized to improve your lifestyle

Target Market(s)

Homeowners aged 35-65. Women are primarily the decision makers.

Industry/Entity Type

It Company

Requirements
Must have
• Images, graphic representations of what's going on.
Should not have
• We want to stay away from a giant block of text as a brochure

```html
<!DOCTYPE html>
<html lang="en">
<head>
<meta charset="utf-8">
<title>Maple Dwelling Bundles – Brochure Cover</title>
<link rel="stylesheet" href="https://fonts.googleapis.com/css2?family=Questrial&display=swap">
<style>
  :root {
    --charcoal: #2f393a;
    --sky-pale: #bfe0f4;
    --sky-light: #6fb6ea;
    --sky-mid: #3d8fdc;
    --panel-bright: #2f6fd0;
    --panel-mid: #1a4bb0;
    --panel-deep: #0b2a86;
    --lime: #c4d82e;
    --ink: #3a3f41;
    --white: #ffffff;
    --brand-grey: #8e9496;
  }
  html, body {
    margin: 0;
    padding: 0;
    width: 1200px;
    height: 856px;
    overflow: hidden;
    background: var(--white);
  }
  .cover {
    position: relative;
    width: 1200px;
    height: 856px;
    font-family: "Questrial", "Century Gothic", sans-serif;
    background: var(--white);
  }
  .cover__topbar {
    position: absolute;
    left: 0; top: 0;
    width: 100%;
    height: 75px;
    background: var(--charcoal);
  }
  .cover__photo {
    position: absolute;
    left: 0; top: 75px;
    width: 1200px;
    height: 605px;
    display: block;
  }
  .cover__headline-box {
    position: absolute;
    left: 0; top: 362px;
    width: 793px;
    height: 318px;
    background: var(--lime);
    opacity: 0.92;
  }
  .cover__headline {
    margin: 0;
    font-weight: 400;
  }
  .cover__headline-lead,
  .cover__headline-rest {
    position: absolute;
    left: 46px;
    line-height: 1;
    white-space: nowrap;
  }
  .cover__headline-lead {
    top: 432px;
    font-size: 88px;
    color: var(--white);
    letter-spacing: 1px;
  }
  .cover__headline-rest {
    top: 541px;
    font-size: 69px;
    color: var(--ink);
    letter-spacing: 0.5px;
  }
  .cover__footer {
    position: absolute;
    left: 0; top: 680px;
    width: 100%;
    height: 176px;
    display: flex;
    align-items: center;
    justify-content: center;
    gap: 24px;
  }
  .brand__mark {
    width: 86px;
    height: 86px;
    border-radius: 50%;
    background: var(--brand-grey);
  }
  .brand__name {
    font-size: 104px;
    line-height: 1;
    color: var(--brand-grey);
    font-weight: 400;
    margin-top: -14px;
  }
</style>
</head>
<body>
  <main class="cover">
    <div class="cover__topbar"></div>
    <svg class="cover__photo" viewBox="0 0 1200 605" role="img" aria-label="Rows of rooftop solar panels rising diagonally against a bright blue sky">
      <defs>
        <linearGradient id="photo-tones" gradientUnits="userSpaceOnUse" x1="700" y1="-10" x2="520" y2="440">
          <stop offset="0" stop-color="var(--sky-mid)"/>
          <stop offset="0.38" stop-color="var(--sky-light)"/>
          <stop offset="0.5" stop-color="var(--sky-light)"/>
          <stop offset="0.56" stop-color="var(--panel-bright)"/>
          <stop offset="0.78" stop-color="var(--panel-mid)"/>
          <stop offset="1" stop-color="var(--panel-deep)"/>
        </linearGradient>
        <radialGradient id="sky-glow" cx="1150" cy="420" r="320" gradientUnits="userSpaceOnUse">
          <stop offset="0" stop-color="var(--sky-pale)" stop-opacity="0.7"/>
          <stop offset="1" stop-color="var(--sky-pale)" stop-opacity="0"/>
        </radialGradient>
      </defs>
      <rect width="1200" height="605" fill="url(#photo-tones)"/>
      <rect width="1200" height="605" fill="url(#sky-glow)"/>
    </svg>
    <div class="cover__headline-box"></div>
    <h1 class="cover__headline">
      <span class="cover__headline-lead">BRING</span>
      <span class="cover__headline-rest">YOUR HOME TO LIFE</span>
    </h1>
    <footer class="cover__footer">
      <span class="brand__mark"></span>
      <span class="brand__name">mapleau</span>
    </footer>
  </main>
</body>
</html>
```